Marlowby Services Website Design

We have most content but require a professional design. We have a logo already and will need it utilized along with several of the photos from the attached documentation.
First page should have our mission and Vision and the synapsis provided in the word document. Visitors will be prompted to select from one of our 3 divisions from this page.
Each division will have the same list of tabs : About, Services, Safety, Careers and Contact.
Photos on each divisions page should be representative of the divisions offerings. The word doc attached contains the requested content and we are open to edits that would complement and fill the website.
I like the Quorvane site www.quorvane.example - they are our competition so cant be modeled directly after this.
Please include prompts to request quote at each service page. align the format of the geotechnical page to the other 2 divisions.
I used chat gpt for some of the content so will need it optimized for SCO.

```html
<!DOCTYPE html>
<html lang="en">
<head>
<meta charset="utf-8">
<title>Marlowby Services</title>
<link href="https://fonts.googleapis.com/css2?family=Orbitron:wght@600;700;800&family=Lato:wght@400;700&display=swap" rel="stylesheet">
<style>
:root{
  --red:#ee1c25;
  --ink:#111111;
  --text:#4a4a4a;
  --white:#ffffff;
  --footer:#000000;
  --line:#e6e6e6;
}
*{margin:0;padding:0;box-sizing:border-box}
html,body{width:1200px;height:2672px;overflow:hidden;background:var(--white)}
body{position:relative;font-family:'Lato',sans-serif;color:var(--text)}
.abs{position:absolute}
.display{font-family:'Orbitron',sans-serif;color:var(--ink);font-weight:700}
.btn{position:absolute;background:var(--red);color:var(--white);border-radius:20px;font:700 15px 'Lato',sans-serif;display:flex;align-items:center;justify-content:center}

/* header */
.site-header{position:absolute;left:0;top:0;width:1200px;height:85px;background:var(--white)}
.brand{position:absolute;left:110px;top:16px;font:800 44px 'Orbitron',sans-serif;color:var(--red);letter-spacing:2px}
.main-nav{position:absolute;left:520px;top:34px;display:flex;gap:24px;font-size:15px;color:var(--ink)}
.header-cta{left:950px;top:24px;width:138px;height:38px}

/* hero */
.hero{position:absolute;left:0;top:85px;width:1200px;height:600px;background:linear-gradient(180deg,#5b4f43 0%,#6d5f50 35%,#4a4037 75%,#2f2923 100%)}
.hero-photo{position:absolute;inset:0;background:radial-gradient(ellipse at 50% 55%,rgba(210,210,210,.35),rgba(0,0,0,0) 55%)}
.hero-copy{position:absolute;left:0;width:1200px;text-align:center;color:var(--white)}
.hero-welcome{top:195px;font:700 38px 'Lato',sans-serif}
.hero-title{top:245px;font:800 76px 'Orbitron',sans-serif;letter-spacing:2px}
.hero-cta{left:532px;top:359px;width:137px;height:38px}

/* vision */
.vision-photo{left:111px;top:771px;width:429px;height:386px;border-radius:10px;background:linear-gradient(180deg,#8fb1d6 0%,#b8cde0 45%,#5f7a55 62%,#9aa0a4 78%,#454a4f 100%)}
.vision-title{left:598px;top:778px;font-size:39px}
.vision-text{left:599px;top:846px;width:490px;font-size:15px;line-height:26px}
.vision-text p{margin-bottom:21px}
.vision-cta{left:600px;top:1103px;width:137px;height:38px}

/* divisions */
.section-title{left:0;width:1200px;text-align:center;font-size:39px}
.division-card{position:absolute;top:1312px;width:309px;height:455px;background:var(--white);border:1px solid var(--line);border-radius:6px;box-shadow:0 2px 8px rgba(0,0,0,.12);text-align:center}
.division-photo{position:absolute;left:8px;top:8px;width:292px;height:196px;border-radius:6px}
.division-name{position:absolute;left:10px;right:10px;top:230px;font:700 19px 'Orbitron',sans-serif;color:var(--ink);line-height:22px}
.division-text{position:absolute;left:30px;right:30px;top:290px;font-size:15px;line-height:26px}
.division-card .btn{left:86px;top:386px;width:137px;height:38px}

/* service */
.service{position:absolute;top:1928px;width:300px;text-align:center}
.service svg{display:block;margin:0 auto}
.service-name{margin-top:26px;font:700 22px 'Orbitron',sans-serif;color:var(--ink)}
.service-text{margin-top:16px;font-size:15px;line-height:22px}
.service .btn{position:relative;margin:22px auto 0;width:137px;height:38px}
.carousel-arrow{position:absolute;top:2033px;width:30px;height:30px;border-radius:50%;background:var(--red)}

/* footer */
.site-footer{position:absolute;left:0;top:2270px;width:1200px;height:360px;background:var(--footer);color:var(--white)}
.footer-title{position:absolute;top:68px;font:700 20px 'Orbitron',sans-serif;color:var(--white)}
.quick-links{position:absolute;left:110px;top:128px;list-style:none;font-size:15px;line-height:26px}
.contact-item{position:absolute;left:352px;display:flex;gap:10px}
.contact-item b{display:block;font-size:17px}
.contact-item span{display:block;font-size:13px;line-height:22px}
.newsletter-text{position:absolute;left:625px;top:126px;width:240px;font-size:15px;line-height:22px}
.newsletter-input{position:absolute;left:625px;top:187px;width:229px;height:40px;border-radius:20px;background:var(--white);color:#555;font-size:11px;display:flex;align-items:center;padding-left:24px;gap:8px}
.subscribe{left:625px;top:242px;width:229px;height:40px}
.social{position:absolute;left:974px;display:flex;align-items:center;gap:12px;font-size:15px}
.social i{display:block;width:22px;height:22px;background:var(--white);border-radius:3px}
.copyright{position:absolute;left:0;top:2630px;width:1200px;height:42px;background:var(--red);color:var(--white);font-size:13px;display:flex;align-items:center;justify-content:center}
</style>
</head>
<body>

<header class="site-header">
  <div class="brand">MARLOWBY</div>
  <nav class="main-nav"><span>Home</span><span>About Us</span><span>Services</span><span>Division</span><span>Contact Us</span></nav>
  <div class="btn header-cta">Get Started</div>
</header>

<section class="hero">
  <div class="hero-photo" role="img" aria-label="Aerial view of a white aerial lift truck parked on a dirt lot beside a fence"></div>
  <div class="hero-copy hero-welcome abs">Welcome To</div>
  <div class="hero-copy hero-title abs">MARLOWBY</div>
  <div class="btn hero-cta">Contact Us</div>
</section>

<section>
  <div class="vision-photo abs" role="img" aria-label="Lift operator in an orange shirt at the controls of an aerial platform"></div>
  <h2 class="display vision-title abs">Our Vision And Mission</h2>
  <div class="vision-text abs">
    <p>To be the leading provider of aerial access, geotechnical drilling, and service solutions, setting the standard for excellence in safety, efficiency, and environmental stewardship.</p>
    <p>At Marlowby, our mission is to deliver unparalleled aerial access, geotechnical drilling, and service and maintenance solutions, consistently exceeding our clients' expectations. We strive to achieve this by investing in cutting-edge technology, fostering a culture of safety and continuous improvement, and prioritizing environmental sustainability.</p>
  </div>
  <div class="btn vision-cta">Read More</div>
</section>

<section>
  <h2 class="display section-title abs" style="top:1235px">Division</h2>
  <article class="division-card" style="left:111px">
    <div class="division-photo" role="img" aria-label="Aerial view of a lift raising a sign above a small town" style="background:linear-gradient(180deg,#a9a59a,#8d8f86 50%,#6c7264)"></div>
    <h3 class="division-name">Aerial Access</h3>
    <p class="division-text">Ut enim ad minim veniam, quis ullamco laboris nisi ut aliquip ex ea commodo consequat.</p>
    <div class="btn">Learn More</div>
  </article>
  <article class="division-card" style="left:443px">
    <div class="division-photo" role="img" aria-label="Crane boom beside a tall white tower under blue sky" style="background:linear-gradient(180deg,#3f78c4,#8cb3dc 65%,#5d7a45)"></div>
    <h3 class="division-name">Geotechnical Drilling</h3>
    <p class="division-text">Ut enim ad minim veniam, quis ullamco laboris nisi ut aliquip ex ea commodo consequat.</p>
    <div class="btn">Learn More</div>
  </article>
  <article class="division-card" style="left:776px">
    <div class="division-photo" role="img" aria-label="Overhead view of a lift truck on a dry field" style="background:linear-gradient(180deg,#8b7a5c,#6d5e48 50%,#3e372c)"></div>
    <h3 class="division-name">Renewable Energy Services</h3>
    <p class="division-text">Ut enim ad minim veniam, quis ullamco laboris nisi ut aliquip ex ea commodo consequat.</p>
    <div class="btn">Learn More</div>
  </article>
</section>

<section>
  <h2 class="display section-title abs" style="top:1846px">Customer Service</h2>
  <div class="carousel-arrow" style="left:61px"><svg width="30" height="30"><path d="M17 9l-6 6 6 6" fill="none" stroke="#fff" stroke-width="2.5"/></svg></div>
  <div class="carousel-arrow" style="left:1109px"><svg width="30" height="30"><path d="M13 9l6 6-6 6" fill="none" stroke="#fff" stroke-width="2.5"/></svg></div>

  <div class="service" style="left:89px">
    <svg width="76" height="76" viewBox="0 0 76 76" fill="none" stroke="#ee1c25" stroke-width="3"><path d="M38 6l26 10v20c0 18-12 28-26 34C24 64 12 54 12 36V16z"/><path d="M26 38l9 9 16-18"/></svg>
    <div class="service-name">Delivering safe</div>
    <p class="service-text">Excepteur sint occaecat cupidatat non proident, sunt in culpa qui officia deserunt mollit anim id est laborum.</p>
    <div class="btn">Read More</div>
  </div>
  <div class="service" style="left:449px">
    <svg width="100" height="76" viewBox="0 0 100 76" fill="none" stroke="#ee1c25" stroke-width="3"><rect x="4" y="4" width="18" height="12"/><path d="M20 14l44 24"/><rect x="8" y="40" width="60" height="20"/><path d="M68 44h16l10 10v6H68"/><circle cx="22" cy="64" r="6"/><circle cx="46" cy="64" r="6"/><circle cx="82" cy="64" r="6"/></svg>
    <div class="service-name">Construction</div>
    <p class="service-text">Excepteur sint occaecat cupidatat non proident, sunt in culpa qui officia deserunt mollit anim id est laborum.</p>
    <div class="btn">Read More</div>
  </div>
  <div class="service" style="left:809px">
    <svg width="76" height="76" viewBox="0 0 76 76" fill="none" stroke="#ee1c25" stroke-width="3"><circle cx="38" cy="38" r="22"/><circle cx="38" cy="38" r="9"/><path d="M38 4v10M38 62v10M4 38h10M62 38h10M14 14l7 7M55 55l7 7M62 14l-7 7M14 62l7-7"/></svg>
    <div class="service-name">Utility</div>
    <p class="service-text">Excepteur sint occaecat cupidatat non proident, sunt in culpa qui officia deserunt mollit anim id est laborum.</p>
    <div class="btn">Read More</div>
  </div>
</section>

<footer class="site-footer">
  <h4 class="footer-title" style="left:110px">Quick Links</h4>
  <ul class="quick-links"><li>Home</li><li>About Us</li><li>Services</li><li>Division</li><li>Contact Us</li></ul>

  <h4 class="footer-title" style="left:352px">Contact Details</h4>
  <div class="contact-item" style="top:120px"><svg width="16" height="20" viewBox="0 0 16 20"><path d="M8 1a6 6 0 0 0-6 6c0 5 6 12 6 12s6-7 6-12a6 6 0 0 0-6-6z" fill="#fff"/><circle cx="8" cy="7" r="2.3" fill="#000"/></svg><div><b>Address</b><span>48 Ridgeline Way, Excepteur<br>sint occaecat cupidatat.</span></div></div>
  <div class="contact-item" style="top:196px"><svg width="16" height="16" viewBox="0 0 16 16"><path d="M3 1l3 3-2 2c1 3 3 5 6 6l2-2 3 3-2 2C7 15 1 9 1 3z" fill="#fff"/></svg><div><b>Phone</b><span>+1 555 010 0142</span></div></div>
  <div class="contact-item" style="top:250px"><svg width="16" height="16" viewBox="0 0 16 16"><rect x="1" y="3" width="14" height="10" fill="#fff"/><path d="M1 3l7 6 7-6" fill="none" stroke="#000" stroke-width="1.3"/></svg><div><b>Email</b><span>info@marlowby.example</span></div></div>

  <h4 class="footer-title" style="left:625px">Join Our Newsletter</h4>
  <p class="newsletter-text">Excepteur sint occaecat cupidatat non proident, est laborum.</p>
  <div class="newsletter-input"><svg width="16" height="12" viewBox="0 0 16 12"><rect x="0" y="0" width="16" height="12" fill="#ee1c25"/><path d="M0 0l8 7 8-7" fill="none" stroke="#fff" stroke-width="1.3"/></svg>Enter Your Email</div>
  <div class="btn subscribe">Subscribe</div>

  <h4 class="footer-title" style="left:974px">Follow Us</h4>
  <div class="social" style="top:132px"><i></i>Social Feed</div>
  <div class="social" style="top:175px"><i></i>News Stream</div>
  <div class="social" style="top:218px"><i></i>Pro Network</div>
</footer>
<div class="copyright">Copyright © 2024 Marlowby. All rights reserved.</div>

</body>
</html>
```